wealth management firm, professional group, new model

we have a logo that works but we need a card, white background using our colors...clean look

our tag line if can be used in

Steady Counsel for Lasting Growth

```html
<!DOCTYPE html>
<html lang="en">
<head>
<meta charset="utf-8">
<title>Arven Wealth Partners – Business Card</title>
<link href="https://fonts.googleapis.com/css2?family=Montserrat:wght@300;400&family=Archivo+Narrow:wght@600&family=Arimo:wght@400&display=swap" rel="stylesheet">
<style>
  :root {
    --navy: #1b2d4f;
    --accent-blue: #2c4e8c;
    --paper: #fbfbfc;
    --ink: #1f2f55;
    --muted: #7c87a0;
    --backdrop-top: #a9bdd6;
    --backdrop-bottom: #7f8ea6;
  }
  * { margin: 0; padding: 0; box-sizing: border-box; }
  html, body { width: 1200px; height: 1200px; overflow: hidden; }
  body {
    background: linear-gradient(160deg, var(--backdrop-top), var(--backdrop-bottom));
    font-family: "Montserrat", sans-serif;
    position: relative;
  }
  .card {
    position: absolute;
    left: 250px;
    width: 700px;
    height: 400px;
    border-radius: 6px;
    overflow: hidden;
    box-shadow: 0 18px 40px rgba(20, 35, 65, 0.28);
  }

  /* Front */
  .card-front { top: 150px; background: var(--navy); color: #fff; }
  .front-band {
    position: absolute; top: 0; right: 120px; width: 70px; height: 100%;
    background: var(--paper);
  }
  .front-band-line {
    position: absolute; top: 0; right: 112px; width: 4px; height: 100%;
    background: var(--accent-blue);
  }
  .front-brand { position: absolute; left: 70px; top: 120px; }
  .front-name {
    font-weight: 300; font-size: 66px; letter-spacing: 0.42em; line-height: 1;
  }
  .front-sub {
    margin-top: 14px; font-weight: 400; font-size: 22px; letter-spacing: 0.2em;
  }
  .tagline {
    position: absolute; left: 70px; bottom: 62px;
    font-weight: 400; font-size: 17px; letter-spacing: 0.12em; text-transform: uppercase;
  }

  /* Back */
  .card-back { top: 650px; background: var(--paper); color: var(--ink); }
  .back-edge {
    position: absolute; left: 0; right: 0; bottom: 0; height: 8px; background: var(--navy);
  }
  .back-brand {
    position: absolute; right: 60px; top: 70px;
    font-weight: 300; font-size: 46px; letter-spacing: 0.42em; color: var(--ink);
  }
  .person { position: absolute; left: 60px; top: 150px; }
  .person-name {
    font-family: "Archivo Narrow", sans-serif; font-weight: 600; font-size: 34px;
    letter-spacing: 0.01em; text-transform: uppercase; line-height: 1;
  }
  .person-title {
    margin-top: 6px; font-size: 14px; letter-spacing: 0.22em; color: var(--muted);
  }
  .contacts {
    position: absolute; left: 60px; top: 250px; list-style: none;
    font-family: "Arimo", sans-serif; font-size: 17px; line-height: 1.25;
  }
  .contacts li { display: flex; align-items: flex-start; gap: 10px; margin-bottom: 6px; }
  .contacts svg { flex: none; width: 18px; height: 18px; margin-top: 1px; }
</style>
</head>
<body>

<section class="card card-front" aria-label="Card front">
  <div class="front-band"></div>
  <div class="front-band-line"></div>
  <div class="front-brand">
    <div class="front-name">ARVEN</div>
    <div class="front-sub">WEALTH PARTNERS</div>
  </div>
  <p class="tagline">Steady Counsel for Lasting Growth</p>
</section>

<section class="card card-back" aria-label="Card back">
  <div class="back-brand">ARVEN</div>
  <div class="person">
    <h1 class="person-name">Daniel Hale</h1>
    <p class="person-title">Managing Director</p>
  </div>
  <ul class="contacts">
    <li>
      <svg viewBox="0 0 18 18"><circle cx="9" cy="9" r="9" fill="#1f2f55"/><path d="M9 4a3 3 0 0 0-3 3c0 2.3 3 6 3 6s3-3.7 3-6a3 3 0 0 0-3-3zm0 4.2A1.2 1.2 0 1 1 9 5.8a1.2 1.2 0 0 1 0 2.4z" fill="#fff"/></svg>
      <span>48 Harbor Lane<br>Newport, RI 02840, United States</span>
    </li>
    <li>
      <svg viewBox="0 0 18 18"><circle cx="9" cy="9" r="9" fill="#1f2f55"/><path d="M6.2 4.8l1.4-.3.9 2-1 .8a6 6 0 0 0 2.8 2.8l.8-1 2 .9-.3 1.4c-3.9.3-6.9-2.7-6.6-6.6z" fill="#fff"/></svg>
      <span>(555) 014-2290</span>
    </li>
    <li>
      <svg viewBox="0 0 18 18"><circle cx="9" cy="9" r="9" fill="#1f2f55"/><rect x="4.5" y="6" width="9" height="6.5" fill="#fff"/><path d="M4.5 6l4.5 3.6L13.5 6" fill="none" stroke="#1f2f55" stroke-width="1"/></svg>
      <span>info@arvenwealth.com</span>
    </li>
    <li>
      <svg viewBox="0 0 18 18"><circle cx="9" cy="9" r="9" fill="#1f2f55"/><g fill="none" stroke="#fff" stroke-width="1"><circle cx="9" cy="9" r="4.5"/><ellipse cx="9" cy="9" rx="2" ry="4.5"/><path d="M4.5 9h9"/></g></svg>
      <span>arvenwealth.com</span>
    </li>
  </ul>
  <div class="back-edge"></div>
</section>

</body>
</html>
```